Clean business card with logo provided

I want a card that will stand out among the masses. I need the color and image to show professionalism and yet have a family appeal showing that I only deal with win/win scenarios. The back of the card will be used to take notes about the individual so I can use that in my database entry. I like modern design but need professionalism in it also. It needs to fit my "clean, safe, and affordable housing" motto. I need to be able to write on the file and update the card details for my employees.

Target Market(s)

Investors looking to make investment income through real estate

Industry/Entity Type

Real Estate

Contact Information for Business Card

Brent Kovalich
blank address, city, st, zip code
480-555-3174
brentkovalich@ridgeworthrentals.example
www.ridgeworthrentals.example

Font styles to use
Sans Serif

Requirements
Must have
• I would like the back of the card to have lines for info. example
• Met/Visited: Date:
• Interets:
Nice to have
• I want the cards color to match the logo background color. Font with details to be san serif and black. I want the card rectangular with square corners. Standard business card size. I would like to see cards designed with both images to see which i prefer more.

```html
<!DOCTYPE html>
<html lang="en">
<head>
<meta charset="utf-8">
<title>Ridgeworth Rentals LLC – Business Card</title>
<link rel="stylesheet" href="https://fonts.googleapis.com/css2?family=Open+Sans:wght@400;600&display=swap">
<style>
  :root {
    --stage: #000000;
    --teal: #00b6cc;
    --teal-text: #14aec4;
    --white: #ffffff;
    --ink: #111111;
    --dots: #222222;
  }
  * { margin: 0; padding: 0; box-sizing: border-box; }
  html, body {
    width: 1200px; height: 900px; overflow: hidden;
    background: var(--stage);
    font-family: "Open Sans", Arial, sans-serif;
  }
  .stage { position: relative; width: 1200px; height: 900px; }
  .card {
    position: absolute; top: 271px; width: 457px; height: 281px;
    border-radius: 14px; overflow: hidden;
  }
  .card--front { left: 137px; background: var(--teal); }
  .card--back { left: 626px; background: var(--white); }

  .brand { position: absolute; display: flex; flex-direction: column; }
  .brand__row { display: flex; align-items: center; gap: 10px; }
  .brand__name {
    font-weight: 400; font-size: 18px; letter-spacing: 1.5px; line-height: 1;
    white-space: nowrap;
  }
  .brand__dot { width: 14px; height: 14px; border-radius: 50%; flex: none; }
  .brand__tagline { font-size: 8.5px; margin-top: 14px; white-space: nowrap; }

  .card--front .brand { left: 34px; top: 46px; }
  .card--front .brand__name, .card--front .brand__tagline { color: var(--white); }
  .card--front .brand__dot { background: var(--ink); }

  .card--back .brand { left: 114px; top: 82px; }
  .card--back .brand__name, .card--back .brand__tagline { color: var(--teal-text); }
  .card--back .brand__dot { background: var(--ink); }

  .holder { position: absolute; left: 204px; top: 128px; color: var(--ink); }
  .holder__name { font-size: 16px; font-weight: 600; line-height: 1; }
  .holder__address { margin-top: 20px; font-size: 12.5px; line-height: 14px; }
  .contact {
    list-style: none; margin-top: 20px; color: var(--white);
    font-size: 12px; letter-spacing: -0.2px;
  }
  .contact li { display: flex; align-items: center; gap: 9px; height: 19px; white-space: nowrap; }
  .contact svg { width: 9px; height: 9px; flex: none; }

  .notes { position: absolute; left: 86px; top: 153px; list-style: none; }
  .notes li { display: flex; align-items: flex-end; height: 33px; }
  .notes__label { color: var(--teal-text); font-size: 14px; font-weight: 600; white-space: nowrap; }
  .notes__line {
    flex: none; margin-left: 6px; margin-bottom: 4px;
    border-bottom: 2px dotted var(--dots);
  }
</style>
</head>
<body>
<main class="stage">
  <section class="card card--front" aria-label="Card front">
    <div class="brand">
      <div class="brand__row">
        <span class="brand__name">RIDGEWORTH RENTALS LLC</span>
        <span class="brand__dot"></span>
      </div>
      <span class="brand__tagline">Providing clean, safe, and affordable housing</span>
    </div>
    <div class="holder">
      <p class="holder__name">Brent Kovalich</p>
      <p class="holder__address">12345, Address Goes Here<br>Country Name, 123456</p>
      <ul class="contact">
        <li><svg viewBox="0 0 10 10"><path d="M2 0.5 L3.6 2.6 L2.8 3.6 Q4 6 6.4 7.2 L7.4 6.4 L9.5 8 L8.4 9.5 Q1 8 0.5 1.6 Z" fill="#111"/></svg>480-555-3174</li>
        <li><svg viewBox="0 0 10 10"><rect x="0.5" y="2" width="9" height="6.5" fill="#111"/><path d="M0.8 2.3 L5 5.6 L9.2 2.3" stroke="#00b6cc" stroke-width="0.9" fill="none"/></svg>brentkovalich@ridgeworthrentals.example</li>
        <li><svg viewBox="0 0 10 10"><circle cx="5" cy="5" r="4.5" fill="#111"/><path d="M0.5 5 H9.5 M5 0.5 Q2.5 5 5 9.5 M5 0.5 Q7.5 5 5 9.5" stroke="#00b6cc" stroke-width="0.7" fill="none"/></svg>www.ridgeworthrentals.example</li>
      </ul>
    </div>
  </section>

  <section class="card card--back" aria-label="Card back">
    <div class="brand">
      <div class="brand__row">
        <span class="brand__name">RIDGEWORTH RENTALS LLC</span>
        <span class="brand__dot"></span>
      </div>
      <span class="brand__tagline">Providing clean, safe, and affordable housing</span>
    </div>
    <ul class="notes">
      <li><span class="notes__label">Visited Date:</span><span class="notes__line" style="width:180px;margin-left:16px"></span></li>
      <li><span class="notes__label">Interets:</span><span class="notes__line" style="width:219px;margin-left:10px"></span></li>
      <li><span class="notes__label">Problems:</span><span class="notes__line" style="width:214px"></span></li>
    </ul>
  </section>
</main>
</body>
</html>
```